Counseling Practice Business Card

I need a professional looking business card incorporating my new logo that was just completed. Card needs to incorporate my name and title, description of my specialty, my address, my phone number, my fax number, my email and my website URL. I need to be able to choose design on/with different paper colors and textures.
I do not have a lot of business card ideas so I am open to anything but I want bold,sharp, clear card without additional designs other than my logo (see attached file info). I am open to different color backgrounds or paper colors including black. I do not like traditional brackets around area codes in phone number or dashes between numbers in phone number. Am open to other ways of presenting including periods between numbers as appropriate. I do not know enough to know what I like yet but I want card to coordinate and work together with my logo. My practice emphasizes natural mental health interventions so any use of color (with background paper color or the blue and green in my logo) that elicits nature is nice. In addition to black, any natural brown or wood looking background might be desirable also. Most of the offerings so far look very similar and boring.

Target Market(s)

Potential therapy clients and other professionals

Contact Information for Business Card

Card information:
Gerald M. Whitcombe, Ph.D.
Licensed Clinical Psychologist
Integrative Health Coach
4812 Marlowe Ridge Blvd SE
Suite 310
Duluth, GA 30096
(770) 415-2983 phone
(770) 581-4096 fax
drgeraldwhitcombe@quillmarsh.net
brightfernwellness.net

Font styles to use
Serif
Sans Serif
Other font styles liked:
• anything that you think looks crisp, clear and easily readable

Requirements
Must have
• Any color used should coordinate with my logo design (see attached files).
• Card should be printed horizontally so top and bottom are longest sides of rectangle.
• Background color or paper color should complement and highlight logo. Do not like a white background. black, grey, brown or any color my logo would blend well with.
Nice to have
• I would like designer to utilize color to highlight letters/name or phone-fax-web symbols.
• Bottom edge of card could be highlighted if appropriate to an idea.
Should not have
• I would NOT want the card to have a pure white background at all.
• No clear cards.
• Cards should be oriented with long sides on bottom and top, NOT sides. DO NOT LIKE THIS THIN TALL ORIENTATION.

```html
<!DOCTYPE html>
<html lang="en">
<head>
<meta charset="utf-8">
<title>Brightfern Wellness – Business Card</title>
<link rel="stylesheet" href="https://fonts.googleapis.com/css2?family=Lato:ital,wght@0,400;0,700;1,400&display=swap">
<style>
  :root {
    --page-bg: #d9d6d0;
    --card-top-a: #f1f1ee;
    --card-top-b: #dcdedb;
    --band-a: #1f5a3a;
    --band-b: #123d27;
    --ink-green: #1d4a2c;
    --ink-blue: #23479a;
    --soft-grey: #d4d8d3;
    --contact-grey: #c9cfca;
    --address-tan: #d6c8a6;
  }
  * { margin: 0; padding: 0; box-sizing: border-box; }
  html, body { width: 1200px; height: 970px; overflow: hidden; }
  body {
    background: var(--page-bg);
    font-family: "Lato", Arial, sans-serif;
    position: relative;
  }
  .card {
    position: absolute;
    left: 100px; top: 188px;
    width: 1000px; height: 593px;
    background: linear-gradient(160deg, var(--card-top-a), var(--card-top-b));
    box-shadow: 0 12px 30px rgba(0,0,0,.22);
    overflow: hidden;
  }
  .brand {
    position: absolute;
    left: 91px; top: 122px;
    display: flex; align-items: center; gap: 16px;
  }
  .brand-dot {
    width: 26px; height: 26px; border-radius: 50%;
    background: var(--ink-blue);
  }
  .brand-name {
    font-size: 56px; font-weight: 700;
    color: var(--ink-green);
    letter-spacing: .5px;
  }
  .holder {
    position: absolute;
    right: 51px; top: 320px;
    font-size: 22px; font-weight: 700;
    color: var(--ink-green);
  }
  .holder .degree {
    font-style: italic; font-weight: 400;
    color: var(--ink-blue);
    margin-left: 10px;
  }
  .band {
    position: absolute;
    left: 0; right: 0; bottom: 0;
    height: 237px;
    background: radial-gradient(ellipse at 30% 20%, var(--band-a), var(--band-b) 75%);
  }
  .specialty {
    position: absolute;
    right: 51px; top: 12px;
    font-size: 16px;
    color: var(--soft-grey);
  }
  .contacts {
    position: absolute;
    left: 68px; top: 70px;
    list-style: none;
  }
  .contacts li {
    display: flex; align-items: center; gap: 16px;
    height: 34px;
    font-size: 19px;
    color: var(--contact-grey);
  }
  .contacts svg { width: 21px; height: 18px; fill: var(--contact-grey); flex: none; }
  .address {
    position: absolute;
    right: 51px; top: 120px;
    text-align: right;
    font-style: normal;
    font-size: 18px; font-weight: 700;
    line-height: 30px;
    color: var(--address-tan);
  }
</style>
</head>
<body>
  <div class="card">
    <div class="brand">
      <span class="brand-dot"></span>
      <span class="brand-name">Brightfern Wellness</span>
    </div>

    <div class="holder">Gerald M. Whitcombe<span class="degree">Ph.D</span></div>

    <div class="band">
      <p class="specialty">Licensed Clinical Psychologist/ Integrative Health Coach</p>

      <ul class="contacts">
        <li>
          <svg viewBox="0 0 21 18" aria-hidden="true"><path d="M2 5c0-2 3-3 8.5-3S19 3 19 5v2h-4V5.5h-9V7H2z"/><rect x="4" y="8" width="13" height="8" rx="1.5"/></svg>
          770.415.2983
        </li>
        <li>
          <svg viewBox="0 0 21 18" aria-hidden="true"><rect x="5" y="1" width="11" height="5"/><rect x="1" y="6" width="19" height="8" rx="1.5"/><rect x="5" y="11" width="11" height="6" fill="#123d27"/><rect x="6" y="12" width="9" height="4"/></svg>
          770.581.4096
        </li>
        <li>
          <svg viewBox="0 0 21 18" aria-hidden="true"><path d="M1 3h19v12H1z M2.5 4.5l8 6 8-6" fill="none" stroke="#c9cfca" stroke-width="1.8"/></svg>
          drgeraldwhitcombe@quillmarsh.net
        </li>
        <li>
          <svg viewBox="0 0 21 18" aria-hidden="true"><g fill="none" stroke="#c9cfca" stroke-width="1.6"><circle cx="10.5" cy="9" r="7.5"/><ellipse cx="10.5" cy="9" rx="3.2" ry="7.5"/><path d="M3 9h15"/></g></svg>
          brightfernwellness.net
        </li>
      </ul>

      <address class="address">
        4812 Marlowe Ridge Blvd SE<br>
        Suite 310, Duluth, GA 30096
      </address>
    </div>
  </div>
</body>
</html>
```